Business Cards for new orthopaedic surgery practice

My husband and I are starting our own orthopaedic surgery practice. We are looking for a business card that is uniform, but one will have my name/title and the other will have his. You can just create one design with my name on it for now. But when I choose your design as the winning design I will ask that you add another copy with his name/title.

We are looking for classy, simple, elite all in one. We like dark blues/a little gold/yellow. Something that goes with our logo. We want our logo incorporated. Here is all the info you need:
Business name: RV Bone & Vitality Center
Location: 38517 North Willowmere Ave
Palm Hollow, FL 33498
Phone: 954-218-4063
Fax: 954-582-7341
Email: info@myrvbonecare.example

Names: Lydia Vance, M.D.
Board Certified Hand and Upper Extremity Surgeon

Ebo Dansu, M.D.
Board Certified Hip & Knee Replacement/General Orthopaedic Surgeon

Can decide what you want to put on the back. Maybe a slogan:
Steady Hands. Stronger Lives

I am just going to upload our logo. The only thing is if we select you as the winning design, the location, and phone numbers may change. We will need your help to update that once fully solidified.

Industry/Entity Type

Medical

Contact Information for Business Card

Colors
0054AA
0677BA
7BADD7
CADEEF
E8F1F8
0094D4
00A9DD
6FCCEA
C7EBF8
E9F6FB

Requirements
Must have
• class, appeal,
Should not have
• We want to air on the side of masculine if we are looking at masculine vs. feminine feel. But we still want it classy, sophisticated, and something we will love

```html
<!DOCTYPE html>
<html lang="en">
<head>
<meta charset="utf-8">
<title>RV Bone &amp; Vitality Center — Business Card</title>
<link rel="stylesheet" href="https://fonts.googleapis.com/css2?family=Libre+Baskerville:wght@400;700&family=Arimo:wght@400&display=swap">
<style>
  :root {
    --bg: #e9e9e9;
    --navy-top: #2c3c64;
    --navy-bottom: #1c2a53;
    --navy-ink: #1f2d57;
    --gold: #c9a45c;
    --white: #ffffff;
    --card-light: #ffffff;
  }
  * { box-sizing: border-box; margin: 0; padding: 0; }
  html, body {
    width: 1200px; height: 1200px; overflow: hidden;
    background: var(--bg);
  }
  .canvas { position: relative; width: 1200px; height: 1200px; }
  .card {
    position: absolute; left: 256px; width: 688px; height: 393px;
  }
  .card-front {
    top: 158px;
    background: linear-gradient(to bottom, var(--navy-top), var(--navy-bottom));
    color: var(--white);
    font-family: "Arimo", Arial, sans-serif;
  }
  .card-back {
    top: 653px;
    background: var(--card-light);
    border-right: 2px solid var(--navy-ink);
    border-bottom: 2px solid var(--navy-ink);
  }
  .identity {
    position: absolute; right: 319px; top: 140px; text-align: right;
  }
  .doctor-name {
    font-family: "Libre Baskerville", Georgia, serif;
    font-weight: 700; font-size: 23px; color: var(--gold);
    letter-spacing: 0.3px; line-height: 28px; margin-right: -3px;
    white-space: nowrap;
  }
  .doctor-title { font-size: 16px; line-height: 20px; margin-top: 1px; }
  .address { font-size: 16.5px; line-height: 22px; margin-top: 5px; }
  .divider {
    position: absolute; left: 396px; top: 144px; width: 1px; height: 107px;
    background: var(--white); opacity: 0.85;
  }
  .contacts {
    position: absolute; left: 414px; top: 156px; list-style: none;
    font-size: 16.5px; line-height: 21px;
  }
  .contacts li { display: flex; align-items: center; gap: 10px; white-space: nowrap; }
  .contacts svg { width: 15px; height: 15px; flex: none; fill: var(--gold); }
  .brand {
    position: absolute; left: 0; right: 0; top: 112px;
    display: flex; flex-direction: column; align-items: center; gap: 16px;
  }
  .brand-dot { width: 18px; height: 18px; border-radius: 50%; background: var(--gold); }
  .brand-name {
    font-family: "Libre Baskerville", Georgia, serif; font-weight: 700;
    font-size: 30px; line-height: 40px; color: var(--navy-ink);
    text-align: center; letter-spacing: 1px;
  }
  .slogan {
    position: absolute; left: 0; right: 0; top: 337px; text-align: center;
    font-family: "Arimo", Arial, sans-serif; font-size: 16px;
    letter-spacing: 3.4px; color: var(--navy-ink);
  }
</style>
</head>
<body>
<main class="canvas">
  <section class="card card-front">
    <div class="identity">
      <p class="doctor-name">LYDIA VANCE, M.D.</p>
      <p class="doctor-title">Board Certified Hand and<br>Upper Extremity Surgeon</p>
      <p class="address">38517 North Willowmere Ave<br>Palm Hollow, FL 33498</p>
    </div>
    <div class="divider"></div>
    <ul class="contacts">
      <li><svg viewBox="0 0 16 16" aria-hidden="true"><path d="M3.5 1.5l2.5 0 1.2 3.2-1.6 1.2c.8 1.8 2.2 3.2 4 4l1.2-1.6 3.2 1.2v2.5c0 .8-.7 1.5-1.5 1.5C7 13.5 2.5 9 2 3c0-.8.7-1.5 1.5-1.5z"/></svg>954-218-4063</li>
      <li><svg viewBox="0 0 16 16" aria-hidden="true"><path d="M4 2h7l1 1v3H4z M2 7h12v6H2z M5 10h6v4H5z"/></svg>954-582-7341</li>
      <li><svg viewBox="0 0 16 16" aria-hidden="true"><path d="M1.5 4h13v9h-13z M2.5 5l5.5 4 5.5-4" stroke="#1f2d57" stroke-width="1"/></svg>info@myrvbonecare.example</li>
      <li><svg viewBox="0 0 16 16" aria-hidden="true"><circle cx="8" cy="8" r="6.5"/><path d="M5 5c1 0 2 1 1.5 2S8 9 7 11M10 3.5c0 1.5 1 2 2.5 2.5" stroke="#1f2d57" stroke-width="1.2" fill="none"/></svg>www.myrvbonecare.example</li>
    </ul>
  </section>

  <section class="card card-back">
    <div class="brand">
      <span class="brand-dot"></span>
      <p class="brand-name">RV Bone &amp;<br>Vitality Center</p>
    </div>
    <p class="slogan">STEADY HANDS. STRONGER LIVES</p>
  </section>
</main>
</body>
</html>
```